Academic and Business book cover

I need a book cover for my academic and business book.
The focus is in international / global negotiation and influence (how to negotiate across cultures).
The book will be published on Zelvorn, both in Vaspet and printed edition. therefore I need something that works under Zelvorn guidelines.The final design should be elegant and still be able to stand out against the competition.
I would like to have orange+grey for the text colors on the cover, even if different options are welcome.
Title and my name are in the attached word doc.

Target Market(s)

graduates, Phds, from international business schools. Managers

Industry/Entity Type

Business

Font styles to use
Serif
Sans Serif

Colors

Designer to choose colors to be used in the design.

Requirements
Must have
• The title and my name should have elegant fonts.
Nice to have
• pictures of the world that don't have the "usual" Europe in the centre.

```html
<!DOCTYPE html>
<html lang="en">
<head>
<meta charset="utf-8">
<title>The 4Rs Blueprint — Book Cover</title>
<link rel="stylesheet" href="https://fonts.googleapis.com/css2?family=Marcellus+SC&display=swap">
<style>
  :root {
    --backdrop-light: #f4f4f4;
    --backdrop-dark: #d9d9d9;
    --cover-slate: #7f98a2;
    --band-slate: #5e7280;
    --ink-dark: #25292d;
    --ink-light: #f3f5f6;
    --globe-light: #c9ced3;
    --globe-mid: #5b636b;
    --globe-dark: #15191d;
  }
  * { margin: 0; padding: 0; box-sizing: border-box; }
  html, body {
    width: 1200px;
    height: 1000px;
    overflow: hidden;
  }
  body {
    background: radial-gradient(circle at 50% 40%, var(--backdrop-light), var(--backdrop-dark));
    font-family: "Marcellus SC", serif;
  }
  .book-cover {
    position: absolute;
    left: 270px;
    top: 50px;
    width: 660px;
    height: 900px;
    background: var(--cover-slate);
    box-shadow: 0 12px 36px rgba(0, 0, 0, 0.18);
  }
  .author-name {
    position: absolute;
    top: 48px;
    width: 100%;
    text-align: center;
    font-size: 34px;
    letter-spacing: 2px;
    color: var(--ink-dark);
  }
  .book-title {
    position: absolute;
    top: 112px;
    width: 100%;
    text-align: center;
    font-weight: 400;
    font-size: 78px;
    line-height: 92px;
    letter-spacing: 4px;
    color: var(--ink-dark);
  }
  .cover-emblem {
    position: absolute;
    left: 0;
    top: 330px;
    width: 660px;
    height: 400px;
  }
  .book-subtitle {
    position: absolute;
    top: 776px;
    width: 100%;
    text-align: center;
    font-size: 23px;
    line-height: 30px;
    letter-spacing: 1.5px;
    color: var(--ink-light);
  }
</style>
</head>
<body>
  <main class="book-cover">
    <p class="author-name">Harlen V. Doust</p>
    <h1 class="book-title">The 4Rs<br>Blueprint</h1>

    <svg class="cover-emblem" viewBox="0 0 660 400" xmlns="http://www.w3.org/2000/svg">
      <defs>
        <radialGradient id="globe-shade" cx="38%" cy="30%" r="75%">
          <stop offset="0" stop-color="var(--globe-light)"/>
          <stop offset="0.45" stop-color="var(--globe-mid)"/>
          <stop offset="1" stop-color="var(--globe-dark)"/>
        </radialGradient>
      </defs>
      <g class="stripe-bands" fill="var(--band-slate)">
        <rect x="66" y="20" width="512" height="66"/>
        <rect x="66" y="119" width="512" height="66"/>
        <rect x="66" y="218" width="512" height="62"/>
        <rect x="66" y="321" width="512" height="66"/>
      </g>
      <circle class="globe" cx="322" cy="205" r="181" fill="url(#globe-shade)"
              role="img" aria-label="Globe showing the Americas with latitude and longitude grid"/>
    </svg>

    <p class="book-subtitle">Practical Dialogue and Persuasion<br>Methods for Worldwide Collaboration</p>
  </main>
</body>
</html>
```